High-end construction company needs a business card design

We need a modern looking business card that draws people in, is memorable and looks so good people will want to sick it on their fridges.
On the first side what is needed are:
Logo
My name - Tomasz Brelwik
Title - Managing Director
Website - www.varkelt.co.uk
Email - tomasz@varkelt.co.uk
Telephone - 020 5194 6281
Mobile - 07845139072
On the back side was is needed is a list of all the services we provide:
-Kitchen Renovations
-Bathroom Renovations
-House Renovations
-Garage Conversions
-Extensions
-Loft Conversions
-Conservatories
-Carpentry
-Tiling
-Electrical
-Plumbing & Heating
-Bricklaying
-Landscaping
-Decorating
-Plastering
We would like the colours to be the same shades as on the logo with grey or black for the words.
Target Market(s)
Anyone who needs building work done
Contact Information for Business Card
This business card is for a construction company which strives to deliver excellent service and quality.
The look and feel of the card should represent this.
Requirements
Must have
- On the first side what is needed are:
Logo
My name - Tomasz Brelwik
Title - Managing Director
Website - www.varkelt.co.uk
Email - tomasz@varkelt.co.uk
Telephone - 020 5194 6281
Mobile - 07845139072
Nice to have
- Cool looking features

```html
<!DOCTYPE html>
<html lang="en">
<head>
<meta charset="utf-8">
<title>Varkelt Construction Ltd – Business Card</title>
<link href="https://fonts.googleapis.com/css2?family=Lato:wght@400;700;900&display=swap" rel="stylesheet">
<style>
  :root {
    --stage: #3a3c40;
    --green-dark: #4b9140;
    --green-light: #74bf45;
    --white: #ffffff;
    --ink-grey: #4a4a4a;
    --divider: #9fd08a;
  }
  * { box-sizing: border-box; margin: 0; padding: 0; }
  html, body {
    width: 1200px; height: 900px; overflow: hidden;
    background: var(--stage);
    font-family: "Lato", sans-serif;
  }
  .stage { position: relative; width: 1200px; height: 900px; }

  .card {
    position: absolute;
    width: 560px; height: 320px;
    border-radius: 26px;
    overflow: hidden;
    box-shadow: 0 14px 30px rgba(0,0,0,0.35);
  }

  /* Back side: services */
  .card--back {
    left: 70px; top: 90px;
    background: var(--green-dark);
    color: var(--white);
    text-align: center;
  }
  .brand {
    font-weight: 900;
    line-height: 1;
    letter-spacing: 0.04em;
    text-transform: uppercase;
  }
  .card--back .brand { margin-top: 62px; font-size: 40px; color: var(--white); }
  .card--back .brand-sub { display: block; font-size: 14px; letter-spacing: 0.28em; margin-top: 8px; }
  .services {
    list-style: none;
    margin: 46px auto 0;
    width: 470px;
    font-size: 15.5px;
    line-height: 1.55;
    display: flex; flex-wrap: wrap; justify-content: center;
  }
  .services li { white-space: nowrap; }
  .services li:not(:last-child)::after {
    content: "|"; color: var(--divider); margin: 0 8px;
  }

  /* Front side: contact */
  .card--front {
    left: 570px; top: 490px;
    background: var(--white);
  }
  .wave { position: absolute; inset: 0; width: 100%; height: 100%; }
  .card--front .brand {
    position: absolute; left: 52px; top: 138px;
    font-size: 38px; color: var(--green-dark);
  }
  .card--front .brand-sub { display: block; font-size: 13px; letter-spacing: 0.28em; margin-top: 8px; }
  .person {
    position: absolute; right: 40px; top: 40px; text-align: right;
  }
  .person-name { font-size: 27px; font-weight: 900; color: var(--green-dark); }
  .person-title { font-size: 15px; color: var(--ink-grey); margin-top: 2px; }
  .contacts {
    position: absolute; right: 24px; top: 170px;
    list-style: none; text-align: right;
    color: var(--white); font-size: 14px; line-height: 1.65;
  }
  .contacts li { display: flex; align-items: center; justify-content: flex-end; gap: 10px; white-space: nowrap; }
  .contacts svg { width: 14px; height: 14px; flex: none; }
</style>
</head>
<body>
<main class="stage">

  <section class="card card--back" aria-label="Business card, services side">
    <div class="brand">Varkelt<span class="brand-sub">Construction Ltd</span></div>
    <ul class="services">
      <li>Kitchen Renovations</li>
      <li>Bathroom Renovations</li>
      <li>House Renovations</li>
      <li>Garage Conversions</li>
      <li>Extensions</li>
      <li>Loft Conversions</li>
      <li>Conservatories</li>
      <li>Carpentry</li>
      <li>Tiling</li>
      <li>Electrical</li>
      <li>Plumbing &amp; Heating</li>
      <li>Bricklaying</li>
      <li>Landscaping</li>
      <li>Decorating</li>
      <li>Plastering</li>
    </ul>
  </section>

  <section class="card card--front" aria-label="Business card, contact side">
    <svg class="wave" viewBox="0 0 560 320" preserveAspectRatio="none" aria-hidden="true">
      <path fill="var(--green-dark)" d="M560,96 C470,96 410,118 360,150 C300,190 270,260 200,300 C180,312 160,318 140,320 L560,320 Z"/>
      <path fill="var(--green-light)" d="M70,296 C170,290 240,262 292,200 C258,260 192,290 70,306 Z"/>
      <path fill="none" stroke="var(--white)" stroke-width="5" stroke-linecap="round" d="M492,112 C430,128 390,152 348,188 C306,226 278,284 186,322"/>
    </svg>

    <div class="brand">Varkelt<span class="brand-sub">Construction Ltd</span></div>

    <div class="person">
      <p class="person-name">Tomasz Brelwik</p>
      <p class="person-title">Managing Director</p>
    </div>

    <ul class="contacts">
      <li>020 5194 6281
        <svg viewBox="0 0 16 16" aria-label="Telephone"><path fill="#fff" d="M2 5c0-2 3-3 6-3s6 1 6 3v1h-3V5H5v1H2zM4 7h8l1 7H3z"/><circle cx="8" cy="10.5" r="1.6" fill="var(--green-dark)"/></svg>
      </li>
      <li>07845139072
        <svg viewBox="0 0 16 16" aria-label="Mobile"><rect x="4" y="1" width="8" height="14" rx="1.5" fill="none" stroke="#fff" stroke-width="1.5"/><circle cx="8" cy="12.5" r="0.9" fill="#fff"/></svg>
      </li>
      <li>tomasz@varkelt.co.uk
        <svg viewBox="0 0 16 16" aria-label="Email"><rect x="1" y="3" width="14" height="10" fill="#fff"/><path d="M1 3l7 6 7-6" fill="none" stroke="var(--green-dark)" stroke-width="1.2"/></svg>
      </li>
      <li>www.varkelt.co.uk
        <svg viewBox="0 0 16 16" aria-label="Website"><g fill="none" stroke="#fff" stroke-width="1.2"><circle cx="8" cy="8" r="6.5"/><ellipse cx="8" cy="8" rx="2.8" ry="6.5"/><path d="M1.5 8h13M2.5 4.8h11M2.5 11.2h11"/></g></svg>
      </li>
    </ul>
  </section>

</main>
</body>
</html>
```